Stonebridge Building and Projects business cards

A business card with watermark background (construction work)

Company logo attached

Home improvement projects
House renovations
Bathroom and kitchen renovations
House extensions
New builds and granny flats

Director Omar Haddani
(Phone number)
omar@sbpbuilding.com.au
(Instagram logo) sbp_building

```html
<!DOCTYPE html>
<html lang="en">
<head>
<meta charset="utf-8">
<title>Stonebridge Building and Projects – Business Cards</title>
<link rel="stylesheet" href="https://fonts.googleapis.com/css2?family=Montserrat:wght@600;700&family=Arimo:wght@400&display=swap">
<style>
  :root {
    --page: #2b2624;
    --card: #1a1a1b;
    --blue: #2f78c4;
    --white: #f2f2f2;
    --rule: #8a8a8a;
  }
  * { margin: 0; padding: 0; box-sizing: border-box; }
  html, body { width: 1200px; height: 842px; overflow: hidden; }
  body {
    background: var(--page);
    font-family: "Arimo", Arial, sans-serif;
    color: var(--white);
    display: flex;
    align-items: center;
    justify-content: center;
    gap: 40px;
  }
  .card {
    position: relative;
    width: 560px;
    height: 320px;
    background: var(--card);
    overflow: hidden;
  }

  /* Contact side */
  .card--contact .band {
    position: absolute; left: 0; right: 0; height: 14px; background: var(--blue);
  }
  .band--top { top: 0; }
  .band--bottom { bottom: 0; }
  .contact {
    position: absolute; inset: 0;
    display: flex; flex-direction: column; align-items: center; justify-content: center;
    text-align: center;
  }
  .contact__name {
    font-family: "Montserrat", sans-serif; font-weight: 700;
    font-size: 24px; color: var(--blue); line-height: 1;
  }
  .contact__role { font-size: 16px; margin-top: 4px; }
  .contact__rule { width: 170px; height: 1px; background: var(--rule); margin: 14px 0 12px; }
  .contact__line { font-size: 16px; line-height: 1.35; }
  .contact__line .accent { color: var(--blue); }
  .social-divider { display: flex; align-items: center; gap: 8px; margin: 12px 0 6px; }
  .social-divider .rule { width: 60px; height: 1px; background: var(--rule); }
  .social-divider .mark { width: 16px; height: 16px; background: var(--blue); border-radius: 3px; }
  .contact__handle { font-size: 16px; }

  /* Brand side */
  .tab { position: absolute; background: var(--blue); }
  .tab--right { right: 0; top: 40px; width: 26px; height: 60px; }
  .tab--left { left: 0; top: 180px; width: 44px; height: 70px; }
  .brand {
    position: absolute; left: 0; right: 0; top: 62px;
    text-align: center;
  }
  .brand__name {
    font-family: "Montserrat", sans-serif; font-weight: 700;
    font-size: 26px; line-height: 1.15; color: var(--blue);
  }
  .brand__tagline {
    display: inline-block; margin-top: 8px; padding-bottom: 3px;
    font-size: 14px; color: var(--blue); border-bottom: 1px solid var(--blue);
  }
  .services {
    position: absolute; left: 0; right: 0; top: 208px;
    text-align: center; font-size: 15px; line-height: 1.45;
  }
  .services .sep { color: var(--blue); padding: 0 5px; }
</style>
</head>
<body>

  <section class="card card--contact" aria-label="Business card, contact side">
    <div class="band band--top"></div>
    <div class="band band--bottom"></div>
    <div class="contact">
      <p class="contact__name">Omar Haddani</p>
      <p class="contact__role">Director</p>
      <div class="contact__rule"></div>
      <p class="contact__line">044-555 018 274</p>
      <p class="contact__line">omar@sbpbuilding.com.au</p>
      <p class="contact__line">www.<span class="accent">sbpbuilding</span>.com.au</p>
      <div class="social-divider"><span class="rule"></span><span class="mark"></span><span class="rule"></span></div>
      <p class="contact__handle">sbp_building</p>
    </div>
  </section>

  <section class="card card--brand" aria-label="Business card, brand side">
    <div class="tab tab--right"></div>
    <div class="tab tab--left"></div>
    <div class="brand">
      <p class="brand__name">Stonebridge Building<br>and Projects</p>
      <p class="brand__tagline">Built solid, built right</p>
    </div>
    <div class="services">
      <p>Home improvement projects<span class="sep">|</span>House renovations</p>
      <p>Bathroom and kitchen renovations</p>
      <p>House extensions<span class="sep">|</span>New builds and granny flats</p>
    </div>
  </section>

</body>
</html>
```